Business Card Design Project

After recently finishing a design project for the company logo using markbazaar, it's now time for a business card. Attached to this is the logo.

The requirements for the business card are pretty straightforward:

- A clean, uncomplicated look
- Consistent usage of fonts
- Designs for both single sided and double sided cards
- A modern layout with preferably space to refer to social media accounts and/or downloadable vcards through a qr code
- consistent application of the company colour scheme: red/white. Hex codes for exact colour can be provided

Thanks!

```html
<!DOCTYPE html>
<html lang="en">
<head>
<meta charset="utf-8">
<title>Cornerstone Talent – Business Card</title>
<link href="https://fonts.googleapis.com/css2?family=Open+Sans:wght@400;600;700&display=swap" rel="stylesheet">
<style>
  :root {
    --brand-red: #e31f2b;
    --swoosh-grey: #8a8a8a;
    --ink: #2b2a2a;
    --card-white: #ffffff;
    --backdrop: #ece9e5;
  }
  * { margin: 0; padding: 0; box-sizing: border-box; }
  html, body { width: 960px; height: 1200px; overflow: hidden; }
  body {
    background: var(--backdrop);
    font-family: "Open Sans", sans-serif;
    color: var(--ink);
    position: relative;
  }
  .card {
    position: absolute;
    width: 840px;
    height: 480px;
    background: var(--card-white);
    border-radius: 28px;
    overflow: hidden;
    box-shadow: 0 6px 14px rgba(0,0,0,0.18);
  }
  .card--front { left: 68px; top: 86px; }
  .card--back { left: 60px; top: 638px; }
  .card__art { position: absolute; inset: 0; }

  .wordmark {
    position: absolute;
    display: flex;
    align-items: center;
    gap: 26px;
  }
  .wordmark__square {
    width: 120px;
    height: 120px;
    background: var(--brand-red);
  }
  .wordmark__name {
    font-weight: 600;
    color: var(--ink);
    line-height: 1;
  }
  .wordmark__line { display: block; }
  .wordmark__line--main { font-size: 80px; letter-spacing: -1px; }
  .wordmark__line--sub { font-size: 44px; letter-spacing: 11px; margin-top: 12px; }
  .card--front .wordmark { left: 40px; top: 46px; }
  .card--back .wordmark { left: 136px; top: 162px; }

  .contact { position: absolute; left: 44px; top: 232px; }
  .contact__name { font-size: 24px; font-weight: 700; }
  .contact__role { font-size: 20px; font-weight: 400; }
  .contact__list { list-style: none; margin-top: 22px; font-size: 18px; line-height: 28px; }
  .contact__key { font-weight: 700; font-style: italic; }

  .address {
    position: absolute;
    left: 0; right: 0;
    top: 426px;
    text-align: center;
    color: var(--card-white);
    font-size: 26px;
    font-weight: 400;
  }
</style>
</head>
<body>
  <section class="card card--front">
    <svg class="card__art" width="840" height="480" viewBox="0 0 840 480" aria-hidden="true">
      <path d="M718,0 C740,190 640,320 505,377 C680,340 790,240 840,128 L840,0 Z" fill="var(--swoosh-grey)"/>
      <path d="M0,402 C110,378 300,392 460,392 C640,384 780,260 840,162 L840,480 L0,480 Z" fill="var(--brand-red)"/>
    </svg>
    <div class="wordmark">
      <span class="wordmark__square"></span>
      <span class="wordmark__name">
        <span class="wordmark__line wordmark__line--main">Cornerstone</span>
        <span class="wordmark__line wordmark__line--sub">TALENT</span>
      </span>
    </div>
    <div class="contact">
      <p><span class="contact__name">Your Name - </span><span class="contact__role">Designation</span></p>
      <ul class="contact__list">
        <li><span class="contact__key">t</span> : 123-123-1234</li>
        <li><span class="contact__key">e</span> : info@yourwebsite.com</li>
        <li><span class="contact__key">w</span> : www.cornerstonetalent.com</li>
      </ul>
    </div>
    <p class="address">1234, Street Name, District, City, Country Code.</p>
  </section>

  <section class="card card--back">
    <div class="wordmark">
      <span class="wordmark__square"></span>
      <span class="wordmark__name">
        <span class="wordmark__line wordmark__line--main">Cornerstone</span>
        <span class="wordmark__line wordmark__line--sub">TALENT</span>
      </span>
    </div>
  </section>
</body>
</html>
```